Website for a Psychologist in Private Practice

I need a cool web design for my website: www.drkalvoric.com. I would like it to look professional. Keep all the current content and add: Space for video; radio spots (see Silver Cedar Tunes Logo below for those); Quick Inquiry; Friendora link; 5 star rating on Rivo; a map; reviews from former patients. I am open to suggestions.

Target Market(s)

Those seeking individual and marital counseling.

Industry/Entity Type

Mental Health

Number of Pages Required

1 page

Font styles to use
Sans Serif
Other font styles liked:
• I'm open but no hard to read script

Requirements
Must have
• All the content on my home page with link for video and radio spots. List services and degrees and expertices (pics not necessary).
Nice to have
• A video of me and radio conversations (logo of Silver Cedar Tunes radio attached).
Should not have
• Cartoons, comedy, etc.... I don't need pictures of services (marital, depression, etc...) Just list those.

```html
<!DOCTYPE html>
<html lang="en">
<head>
<meta charset="utf-8">
<title>Dr. Delia K. Kalvoric – Psychologist</title>
<link href="https://fonts.googleapis.com/css2?family=Ubuntu:ital,wght@0,400;0,500;1,400&family=Raleway:wght@500&family=Arimo:ital,wght@0,400;0,700;1,400;1,700&display=swap" rel="stylesheet">
<style>
:root{
  --blue:#2d86c8;
  --blue-dark:#1f6ea9;
  --white:#ffffff;
  --ink:#2b2b2b;
  --footer:#211e1e;
  --line:#c9d3d8;
  --field:#3c4a4e;
  --badge-red:#c8242b;
  --badge-green:#8aa53a;
}
*{box-sizing:border-box;margin:0;padding:0}
html,body{width:783px;height:1200px;overflow:hidden}
body{
  position:relative;
  font-family:"Ubuntu",sans-serif;color:var(--white);
  background:linear-gradient(180deg,#6f8fb0 0%,#a9bfd3 12%,#c6d3de 20%,#3f8ea0 27%,#2aa0ad 40%,#4ab0b2 52%,#8d9c94 62%,#9e8e7e 75%,#8c7a6a 100%);
}
.abs{position:absolute}
.page{position:absolute;left:86px;top:0;width:612px;height:1200px}
/* header */
.header{left:0;top:0;width:612px;height:62px;background:linear-gradient(180deg,rgba(60,80,100,.55),rgba(80,105,125,.45))}
.brand{left:9px;top:20px;font-size:24px;font-weight:500;letter-spacing:.2px}
.share{left:375px;top:34px;width:60px;height:20px;background:#3b5a96;border:1px solid #6f8ec8;font-size:9px;display:flex;align-items:center;justify-content:center;gap:4px;font-family:"Arimo",sans-serif}
.share i{width:9px;height:9px;background:var(--white);display:block}
.rating-badge{left:440px;top:12px;width:42px;height:42px;border-radius:6px;background:var(--badge-red);border:2px solid #fff}
.call{left:496px;top:19px}
.call small{display:block;font-size:10px;margin-left:16px}
.call b{display:block;font-size:15px;font-weight:500;margin-left:17px;margin-top:2px}
.call svg{position:absolute;left:-4px;top:6px}
/* nav */
.nav{left:0;top:62px;width:612px;height:28px;background:var(--blue);display:flex;align-items:center;font-size:11px}
.nav a{color:var(--white);text-decoration:none;padding:0 11px;height:28px;line-height:28px;border-right:1px solid rgba(255,255,255,.25)}
.nav a.current{background:#4d9ad4}
.follow{position:absolute;right:6px;top:0;height:28px;display:flex;align-items:center;gap:5px;font-size:9px}
.follow span{width:21px;height:21px;border-radius:50%;background:#1d5e91;display:block}
.follow span+span{background:#36a5e1}
/* hero */
.hero{left:0;top:90px;width:612px;height:287px;background:linear-gradient(160deg,#3f4b4f 0%,#5f6d6e 40%,#4d585a 65%,#2e3638 100%)}
.hero h1{position:absolute;left:0;width:612px;top:120px;text-align:center;font-family:"Raleway",sans-serif;font-weight:500;font-size:18px;line-height:23px}
.arrow{top:130px;width:29px;height:23px;background:rgba(255,255,255,.85);display:flex;align-items:center;justify-content:center}
/* headings */
.h2{font-size:14.5px}
.rule{height:2px;background:var(--line)}
.rule b{display:block;height:2px;width:60px;background:#222}
.rule.blue{background:var(--blue)}
/* about */
.about-text{left:7px;top:438px;width:392px;font-size:9.3px;line-height:14px;font-family:"Arimo",sans-serif}
.more{color:var(--white);text-decoration:underline;font-size:9.5px}
.degrees{left:0;top:520px;width:398px;height:64px;background:rgba(20,40,45,.45)}
.degrees h3{position:absolute;left:10px;top:6px;font-size:14px;font-weight:400}
.degrees ul{position:absolute;top:31px;list-style:none;font-size:8.6px;line-height:14px}
.degrees li::before{content:"•";margin-right:5px}
.video{left:414px;top:437px;width:191px;height:146px;border:2px solid var(--blue);background:radial-gradient(circle at 50% 45%,#d7b68a 0%,#a98f6e 30%,#4a6a5a 75%,#2f4a3c 100%)}
/* expertise row */
.col-title{font-size:14px;line-height:16px}
.avatar{border-radius:50%;border:2px solid #fff}
.checks{left:14px;top:727px;list-style:none;font-size:9px;line-height:13.8px}
.checks li{display:flex;align-items:center;gap:4px}
.quote-box{left:209px;top:661px;width:186px;height:111px;background:#dcdcdc;border:2px solid #b9b9b9;color:var(--ink);font-family:"Arimo",sans-serif;font-size:9px;line-height:13.5px;padding:5px 9px}
.quote-box cite{position:absolute;right:10px;bottom:14px;font-style:normal;font-size:8px;color:#555}
.field{left:417px;width:181px;height:20px;background:var(--field);font-family:"Arimo",sans-serif;font-size:7.5px;color:#ccd;padding:6px 7px}
.submit{left:417px;top:770px;width:72px;height:22px;background:var(--blue);font-family:"Arimo",sans-serif;font-weight:700;font-size:10px;display:flex;align-items:center;justify-content:center}
/* reviews */
.reviews{left:0;top:822px;width:612px;height:191px;background:rgba(70,70,70,.45)}
.review-text{left:95px;top:62px;width:502px;font-family:"Arimo",sans-serif;font-style:italic;font-size:8.4px;line-height:15.5px}
/* footer */
.footer{left:0;top:1013px;width:612px;height:160px;background:var(--footer);font-family:"Arimo",sans-serif}
.footer h4{position:absolute;top:18px;font-family:"Ubuntu",sans-serif;font-weight:400;font-size:10.5px}
.links{left:9px;top:45px;list-style:none;font-size:8.5px;line-height:14.3px}
.links li:first-child{color:#c6a25a}
.partner{left:138px;width:112px;height:52px;border:2px solid #cfd9e6}
.contact{left:323px;font-size:8.5px;line-height:12px;display:flex;gap:10px}
.contact b{font-weight:400;width:9px}
.poster{left:479px;top:22px;width:122px;height:122px;background:linear-gradient(150deg,#d2305f 0%,#a7446a 25%,#c8a78f 55%,#4f7d3b 100%)}
.copyright{left:0;top:1173px;width:612px;height:27px;background:var(--blue);font-family:"Arimo",sans-serif;font-size:8.5px;display:flex;align-items:center;justify-content:center}
</style>
</head>
<body>
<div class="page">

  <header class="abs header">
    <div class="abs brand">Dr. Delia K. Kalvoric</div>
    <div class="abs share"><i></i>Friendora</div>
    <div class="abs rating-badge" role="img" aria-label="Rivo five star rating badge"></div>
    <div class="abs call">
      <svg width="18" height="18" viewBox="0 0 18 18"><circle cx="9" cy="9" r="8" fill="none" stroke="#fff" stroke-width="1.2"/><path d="M6.5 5c1 0 1 2 .3 2.4.4 1.4 1.5 2.6 2.9 3.1.5-.6 2.3-.6 2.3.4 0 1-1 1.6-2 1.3C7.6 11.5 5.3 9 5 6.5 4.9 5.7 5.6 5 6.5 5z" fill="#fff"/></svg>
      <small>Call Us Today</small>
      <b>555-014-2270</b>
    </div>
  </header>

  <nav class="abs nav">
    <a class="current" href="#">Home</a>
    <a href="#">About Me</a>
    <a href="#">Sessions</a>
    <a href="#">Resources</a>
    <a href="#">BIO</a>
    <a href="#">Customer Reviews</a>
    <a href="#" style="border-right:0">Contact Us</a>
    <div class="follow">Follow Us On <span title="Friendora"></span><span title="Chirpline"></span></div>
  </nav>

  <section class="abs hero" role="img" aria-label="Couple holding hands walking outdoors">
    <h1>Committed To Assisting Our Clients To Overcome,<br>Achieve, And Improve Quality Of Life.</h1>
    <div class="abs arrow" style="left:0"><svg width="8" height="10"><path d="M6 1L2 5l4 4" stroke="#333" stroke-width="2" fill="none"/></svg></div>
    <div class="abs arrow" style="left:583px"><svg width="8" height="10"><path d="M2 1l4 4-4 4" stroke="#333" stroke-width="2" fill="none"/></svg></div>
  </section>

  <!-- about -->
  <h2 class="abs h2" style="left:9px;top:400px;font-weight:400">About Dr. Delia K. Kalvoric</h2>
  <div class="abs rule blue" style="left:6px;top:423px;width:183px"><b style="width:40px"></b></div>
  <p class="abs about-text">While I acknowledge the importance of my education, I also appreciate the role my experiences have played in allowing me to relate so well to others. Allow me to share those I feel are most relevant with you.I survived an abusive childhood that my mother &amp; sister unfortunately did not. &amp; it was my grief &amp; desire to become stronger ...</p>
  <a class="abs more" style="left:346px;top:492px">Read More</a>

  <div class="abs degrees">
    <h3>My Degrees</h3>
    <ul style="left:10px"><li>Doctoral Degree in Clinical Psychology</li><li>Masters Degree in Counseling Psychology</li></ul>
    <ul style="left:214px"><li>Doctoral Internship, Coastline Medical Center</li><li>Masters Internship, Harborview Clinic</li></ul>
  </div>

  <h2 class="abs h2" style="left:413px;top:403px;font-weight:400">View Video</h2>
  <div class="abs rule blue" style="left:413px;top:423px;width:191px"><b style="width:65px"></b></div>
  <div class="abs video" role="img" aria-label="Video introduction from Dr. Kalvoric">
    <svg class="abs" style="left:77px;top:64px" width="20" height="20" viewBox="0 0 20 20"><circle cx="10" cy="10" r="8.5" fill="none" stroke="#fff" stroke-width="1.6"/><path d="M8 6l6 4-6 4z" fill="#fff"/></svg>
  </div>

  <!-- expertise -->
  <div class="abs col-title" style="left:11px;top:612px">My<br>Expertise</div>
  <svg class="abs" style="left:158px;top:614px" width="28" height="30" viewBox="0 0 28 30"><path d="M14 2C7 2 3 7 3 13c0 3 1.5 5 3 6.5V28h11v-4h4c2 0 2-2 2-3v-3l3-1-3-5C22 6 19 2 14 2z" fill="#e7ecef"/><circle cx="12" cy="12" r="4" fill="none" stroke="#8a9aa2" stroke-width="2"/><circle cx="19" cy="17" r="2.5" fill="none" stroke="#8a9aa2" stroke-width="1.6"/></svg>
  <div class="abs rule" style="left:11px;top:646px;width:175px"><b style="width:70px"></b></div>
  <div class="abs avatar" style="left:8px;top:655px;width:68px;height:68px;background:radial-gradient(circle at 50% 40%,#d9b48c,#a27a55 55%,#3c6f9b 100%)" role="img" aria-label="Portrait of Dr. Kalvoric"></div>
  <div class="abs" style="left:83px;top:665px;font-size:13px;line-height:16px">Dr. Delia K.<br>Kalvoric</div>
  <div class="abs" style="left:83px;top:701px;font-size:10px">California # PSY20581</div>
  <ul class="abs checks">
    <li><svg width="8" height="8"><path d="M1 4l2 3 4-6" stroke="#fff" stroke-width="1.6" fill="none"/></svg>Dating, Marriage,</li>
    <li><svg width="8" height="8"><path d="M1 4l2 3 4-6" stroke="#fff" stroke-width="1.6" fill="none"/></svg>Parenting &amp; Professional Relationships</li>
    <li><svg width="8" height="8"><path d="M1 4l2 3 4-6" stroke="#fff" stroke-width="1.6" fill="none"/></svg>Depression &amp; Anxiety Issues</li>
    <li><svg width="8" height="8"><path d="M1 4l2 3 4-6" stroke="#fff" stroke-width="1.6" fill="none"/></svg>Personality Disorders</li>
    <li><svg width="8" height="8"><path d="M1 4l2 3 4-6" stroke="#fff" stroke-width="1.6" fill="none"/></svg>Life Management</li>
  </ul>

  <div class="abs col-title" style="left:209px;top:612px">Radio<br>Conversations</div>
  <svg class="abs" style="left:367px;top:614px" width="20" height="30" viewBox="0 0 20 30"><rect x="5" y="1" width="10" height="17" rx="5" fill="#e7ecef"/><path d="M2 13c0 5 4 8 8 8s8-3 8-8" stroke="#e7ecef" stroke-width="2" fill="none"/><path d="M10 21v6M5 28h10" stroke="#e7ecef" stroke-width="2"/></svg>
  <div class="abs rule" style="left:209px;top:646px;width:182px"><b style="width:75px"></b></div>
  <div class="abs quote-box">
    <span style="font-size:14px;font-weight:700;color:#888">“</span> Lorem ipsum dolor sit ae onsectetuer adipiscing elit, sed diam nonummy nibh euis tincidunt ut laoreetlore gna aliquam erat olutpat. Ut wisi enim adinim veniam, quis strud xerci tation ullamrper suscipit lobortis sl ut al lorem.
    <cite>Lena Marsh</cite>
  </div>
  <a class="abs more" style="left:209px;top:780px">View All</a>

  <div class="abs col-title" style="left:419px;top:612px">Quick<br>Inquiry</div>
  <svg class="abs" style="left:557px;top:617px" width="38" height="27" viewBox="0 0 38 27"><rect x="1" y="1" width="36" height="25" fill="none" stroke="#e7ecef" stroke-width="2"/><path d="M1 1l18 14L37 1M1 26l13-12M37 26L24 14" stroke="#e7ecef" stroke-width="2" fill="none"/></svg>
  <div class="abs rule" style="left:419px;top:646px;width:179px"><b style="width:65px"></b></div>
  <div class="abs field" style="top:662px">Name</div>
  <div class="abs field" style="top:685px">Email</div>
  <div class="abs field" style="top:708px">Phone</div>
  <div class="abs field" style="top:730px;height:35px">Message</div>
  <div class="abs submit">SUBMIT</div>

  <!-- reviews -->
  <section class="abs reviews">
    <h2 class="abs h2" style="left:0;width:612px;text-align:center;top:20px;font-weight:500">Reviews From Former Patients</h2>
    <div class="abs" style="left:207px;top:44px;width:198px;height:2px;background:var(--line)"><div style="margin-left:69px;width:60px;height:2px;background:var(--blue)"></div></div>
    <div class="abs avatar" style="left:7px;top:59px;width:76px;height:76px;background:radial-gradient(circle at 50% 38%,#e2c3a3,#b08a69 40%,#2a3036 80%)" role="img" aria-label="Portrait of a former patient"></div>
    <p class="abs review-text"><span style="font-size:18px;color:#999;font-style:normal;margin-right:4px">“</span>Lorem ipsum dolor sit amet, consectetuer adipiscing elit, sed diam nonummy nibh euismod tincidunt ut laoreet dolore magna aliquam erat volutpat. Ut wisi enim ad minim veniam, quis nostrud exerci tation ullamcorper suscipit lobortis nisl ut aliquip commodo consequat. Duis autem vel eum iriure dolor in hendrerit in vulputate velit esse molestie consequat, vel illum dolore eu feugiat nulla facilisis at vero eros et accumsan et iusto odio dignissimaugue duis dolore te feugait nulla facilisi.</p>
    <div class="abs" style="left:97px;top:134px;font-family:'Arimo',sans-serif;font-style:italic;font-weight:700;font-size:8.5px">.... Lorem Ispum, Manger</div>
    <a class="abs more" style="left:507px;top:148px;font-family:'Arimo',sans-serif;font-size:8.5px">Read more testimonials</a><span class="abs" style="left:601px;top:147px;font-size:9px">»</span>
  </section>

  <!-- footer -->
  <footer class="abs footer">
    <h4 style="left:9px">Quick Links</h4>
    <ul class="abs links">
      <li>Home</li><li>About Me</li><li>Sessions</li><li>Resources</li><li>BIO</li><li>Customer Reviews</li><li>Contact Me</li>
    </ul>
    <h4 style="left:138px">A Portion of All Revenue Is Donated To</h4>
    <div class="abs partner" style="top:41px;background:#fff" role="img" aria-label="Child advocacy partner badge"></div>
    <div class="abs partner" style="top:96px;background:var(--badge-green)" role="img" aria-label="Family support partner badge"></div>
    <h4 style="left:323px">Contact Details</h4>
    <div class="abs" style="left:323px;top:34px;width:124px;border-top:1px dashed #777"></div>
    <div class="abs contact" style="top:49px"><b>A:</b><span>418 Harbor Lane, Suite 210<br>Bayview, CA 90210</span></div>
    <div class="abs contact" style="top:86px"><b>P:</b><span>555-014-2270</span></div>
    <div class="abs contact" style="top:108px"><b>TF:</b><span>555-014-2270</span></div>
    <div class="abs contact" style="top:130px"><b>E:</b><span>dk@drkalvoric.com</span></div>
    <div class="abs poster" role="img" aria-label="Silver Cedar Tunes radio show poster"></div>
  </footer>
  <div class="abs copyright">Copyright © 2016 Dr. Delia K. Kalvoric&nbsp; All rights reserved</div>

</div>
</body>
</html>
```